Meridale Partners Website

Meridale Partners (MP) provide Analytics & Enterprise Performance Management (EPM) advisory & consultancy services. We are passionate about data and making a difference for our clients by working in partnership with them, helping them on their journey to becoming an Meridale Partner. We deliver insights which give our clients a competitive edge and a much deeper understanding of their organisation.

We need a website which shows who we are, what we do and how we do it.

www.meridale-partners.example is our very basic website at the moment. We want to completely revamp it with a corporate look

```html
<!DOCTYPE html>
<html lang="en">
<head>
<meta charset="utf-8">
<title>Meridale Partners</title>
<link href="https://fonts.googleapis.com/css2?family=Poppins:wght@300;400;500;600;700&display=swap" rel="stylesheet">
<style>
:root{
  --navy:#1b2f3c;
  --teal:#2b5468;
  --orange:#d96a34;
  --mist:#f3f7f9;
  --ink:#1e3342;
  --text:#5f6b73;
  --white:#ffffff;
}
*{box-sizing:border-box;margin:0;padding:0}
html,body{width:1200px;height:2926px;overflow:hidden}
body{position:relative;font-family:'Poppins',sans-serif;color:var(--ink);background:var(--white)}
.abs{position:absolute}
a{text-decoration:none;color:inherit}

/* header */
.hero-art{position:absolute;left:0;top:0;width:1200px;height:640px}
.brand{position:absolute;display:flex;align-items:center;gap:12px;color:var(--white);font-weight:600;font-size:20px;line-height:21px;letter-spacing:.5px;text-transform:uppercase}
.brand .dot{width:58px;height:58px;border-radius:50%;border:7px solid var(--white)}
.nav{position:absolute;top:19px;right:60px;display:flex;align-items:center;gap:36px;color:var(--white);font-size:13px;letter-spacing:.3px}
.pill{display:inline-flex;align-items:center;gap:8px;border-radius:20px;font-size:13px;height:36px;padding:0 20px}
.pill-orange{background:var(--orange);color:var(--white)}
.pill-navy{background:var(--navy);color:var(--white);font-weight:600}
.pill-white{background:var(--white);color:var(--ink)}
.nav .pill{font-weight:600}
.hero-title{position:absolute;top:232px;left:0;width:1200px;text-align:center;color:var(--white);font-weight:600;font-size:50px;line-height:50px;letter-spacing:1px}
.hero-sub{position:absolute;top:290px;left:360px;width:480px;text-align:center;color:var(--white);font-size:14px;line-height:23px}
.hero-cta{position:absolute;top:386px;left:523px}
.scroll-btn{position:absolute;left:578px;top:609px;width:44px;height:44px;border-radius:50%;background:var(--orange);border:3px solid var(--white);box-shadow:0 3px 10px rgba(0,0,0,.2);display:flex;align-items:center;justify-content:center}

/* about */
.about-block{position:absolute;left:60px;top:679px;width:130px;height:118px;background:var(--navy)}
.about-photo{position:absolute;left:109px;top:716px;width:381px;height:336px;border-radius:14px;background:linear-gradient(135deg,#e9eef2,#c9d3dc 55%,#2e3f63)}
.eyebrow{color:var(--orange);font-size:12px;text-transform:uppercase}
.h2{font-weight:600;font-size:28px;line-height:37px;text-transform:uppercase;color:var(--ink)}
.body{font-size:14px;line-height:22.5px;color:var(--text)}

/* services */
.services-bg{position:absolute;left:0;top:1110px;width:1200px;height:515px}
.section-mark{position:absolute;left:582px;width:36px;height:36px;border-radius:50%;border:6px solid var(--teal)}
.section-title{position:absolute;left:0;width:1200px;text-align:center;font-weight:600;font-size:26px;text-transform:uppercase;color:var(--ink)}
.service{position:absolute;top:1271px;width:340px;height:299px;text-align:center;border-radius:10px}
.service.is-active{background:var(--teal)}
.service .icon{width:86px;height:86px;border-radius:50%;background:var(--teal);margin:23px auto 0;display:flex;align-items:center;justify-content:center}
.service.is-active .icon{background:var(--white);border:3px solid var(--teal);box-shadow:0 0 0 2px var(--white)}
.service h3{font-weight:500;font-size:17px;margin-top:9px;color:var(--ink)}
.service p{font-size:13.5px;line-height:22.5px;color:var(--text);margin:7px auto 0;width:290px}
.service.is-active h3,.service.is-active p{color:var(--white)}
.read-more{position:absolute;left:0;width:100%;top:258px;font-size:12.5px;color:var(--orange);text-transform:uppercase}

/* process */
.hub{position:absolute;left:161px;top:1847px;width:268px;height:268px;border-radius:50%;background:var(--white);box-shadow:0 0 26px rgba(30,50,66,.12);display:flex;flex-direction:column;align-items:center;justify-content:center;gap:10px}
.hub .dot{width:60px;height:60px;border-radius:50%;background:var(--teal)}
.hub span{font-weight:600;font-size:21px;color:var(--teal)}
.step-icon{position:absolute;width:86px;height:86px;border-radius:50%;background:var(--white);box-shadow:0 0 18px rgba(30,50,66,.14);display:flex;align-items:center;justify-content:center}
.step-icon::before{content:"";position:absolute;inset:8px;border-radius:50%;background:#eef3f6}
.step-icon svg{position:relative}
.node{position:absolute;width:30px;height:30px;border-radius:50%;background:var(--orange);border:4px solid var(--white);box-shadow:0 0 8px rgba(0,0,0,.15)}
.step h4{font-weight:500;font-size:17px;color:var(--ink)}
.step p{font-size:13.5px;line-height:22.5px;color:var(--text);width:380px;margin-top:4px}

/* contact band */
.cta-art{position:absolute;left:0;top:2200px;width:1200px;height:430px}
.cta-title{position:absolute;left:61px;top:2368px;font-weight:600;font-size:28px;line-height:36px;color:var(--white)}
.cta-text{position:absolute;left:61px;top:2409px;width:630px;font-size:14px;line-height:22.5px;color:var(--white)}
.cta-photo{position:absolute;left:764px;top:2224px;width:374px;height:374px;border-radius:50%;background:linear-gradient(140deg,#e8edf1,#b9c9d8 55%,#4f78a6)}

/* footer */
.footer{position:absolute;left:0;top:2624px;width:1200px;height:262px;background:var(--navy);color:var(--white)}
.footer h5{font-weight:500;font-size:14px;padding-bottom:6px;border-bottom:2px solid var(--teal);display:inline-block}
.footer ul{list-style:none;font-size:12px;text-transform:uppercase}
.footer li{height:31.5px}
.contact-row{display:flex;gap:12px;font-size:12.5px;line-height:19px;align-items:flex-start}
.partner{display:flex;align-items:center;gap:10px;font-size:12px}
.partner b{font-weight:500;color:var(--orange);font-size:13px;letter-spacing:1px;text-transform:uppercase}
.partner i{width:2px;height:30px;background:var(--white)}
.social{width:34px;height:34px;border-radius:50%}
.bottom-bar{position:absolute;left:0;top:2886px;width:1200px;height:40px;background:var(--orange);color:var(--white);font-size:12px;text-align:center;line-height:40px}
</style>
</head>
<body>

<!-- hero -->
<svg class="hero-art" viewBox="0 0 1200 640" aria-hidden="true">
  <defs>
    <linearGradient id="cityTone" x1="0" y1="0" x2="0" y2="1">
      <stop offset="0" stop-color="#1b2e4c"/>
      <stop offset=".55" stop-color="#1f4a7a"/>
      <stop offset="1" stop-color="#152b45"/>
    </linearGradient>
  </defs>
  <path d="M0 0H1200V448Q820 655 430 632Q190 616 0 532Z" fill="url(#cityTone)" role="img" aria-label="Night city skyline with illuminated towers"/>
  <path d="M0 532Q190 616 430 632Q530 638 600 638Q420 648 250 625Q90 602 0 570Z" fill="#d96a34"/>
</svg>

<div class="brand" style="left:60px;top:12px">
  <span class="dot"></span><span>Meridale<br>Partners</span>
</div>
<nav class="nav">
  <a href="#who">WHO WE ARE</a>
  <a href="#what">WHAT WE DO</a>
  <a href="#how">HOW WE DO IT</a>
  <a href="#contact">CONTACT US</a>
  <a class="pill pill-orange" href="#contact">
    <svg width="18" height="18" viewBox="0 0 24 24" fill="none" stroke="#fff" stroke-width="1.8"><path d="M5 3h4l2 5-3 2a12 12 0 0 0 6 6l2-3 5 2v4a2 2 0 0 1-2 2A17 17 0 0 1 3 5a2 2 0 0 1 2-2z"/></svg>01 555 0142</a>
</nav>
<h1 class="hero-title">MERIDALE PARTNERS</h1>
<p class="hero-sub">Meridale Partners is an exciting start-up in the Data Analytics and EPM space.</p>
<a class="pill pill-orange hero-cta" href="#contact">CONTACT US
  <svg width="28" height="14" viewBox="0 0 28 14" fill="none" stroke="#fff" stroke-width="1.6"><circle cx="7" cy="7" r="5.5"/><path d="M7 7h19M21 2l5 5-5 5"/></svg></a>
<div class="scroll-btn"><svg width="14" height="20" viewBox="0 0 14 20" fill="none" stroke="#fff" stroke-width="1.6"><rect x="1" y="1" width="12" height="18" rx="6"/><path d="M7 5v4"/></svg></div>

<!-- who we are -->
<section id="who">
  <div class="about-block"></div>
  <div class="about-photo" role="img" aria-label="Consultant in a suit reviewing a report beside a monitor showing bar charts"></div>
  <div class="abs" style="left:592px;top:750px;width:430px">
    <p class="eyebrow">Who we are</p>
    <h2 class="h2" style="margin-top:8px">Welcome to Meridale Partners</h2>
    <p class="body" style="margin-top:10px">MP are a Data Analytics &amp; EPM company, specialising in the implementation and support of Business Intelligence, EPM and Data Analytics business solutions, both in the Cloud and on-premise.</p>
    <a class="pill pill-orange" style="margin-top:43px;height:37px" href="#">READ MORE
      <svg width="28" height="14" viewBox="0 0 28 14" fill="none" stroke="#fff" stroke-width="1.6"><circle cx="7" cy="7" r="5.5"/><path d="M7 7h19M21 2l5 5-5 5"/></svg></a>
  </div>
</section>

<!-- what we do -->
<section id="what">
  <svg class="services-bg" viewBox="0 0 1200 515" aria-hidden="true"><path d="M0 210Q600 -150 1200 75V515H0Z" fill="#f3f7f9"/></svg>
  <div class="section-mark" style="top:1175px"></div>
  <h2 class="section-title" style="top:1218px">What we do</h2>

  <div class="service" style="left:66px">
    <div class="icon"><svg width="44" height="44" viewBox="0 0 44 44" fill="none" stroke="#fff" stroke-width="1.8"><path d="M6 36h32M10 32V24M17 32V18M24 32V22M31 32V12M8 20l9-8 7 5 12-10M30 7h6v6"/></svg></div>
    <h3>Advise &amp; Architech</h3>
    <p>Helping our customers understand the art of the possible and safeguarding their investments by overseeing implementations.</p>
    <a class="read-more" href="#">Read more &#10230;</a>
  </div>
  <div class="service is-active" style="left:427px">
    <div class="icon"><svg width="44" height="44" viewBox="0 0 44 44" fill="none" stroke="#2b5468" stroke-width="1.8"><path d="M12 20a8 8 0 0 1 16-4 6 6 0 1 1 2 11H12a5 5 0 0 1 0-10"/><path d="M16 36l14-14 4 4-14 14h-4z"/><circle cx="33" cy="34" r="4" stroke="#d96a34"/></svg></div>
    <h3>Design &amp; Implement</h3>
    <p>Working with the project management team, through each stage of the project, with clearly defined deliverables and well exercised plans to deliver them.</p>
    <a class="read-more" href="#">Read more &#10230;</a>
  </div>
  <div class="service" style="left:800px">
    <div class="icon"><svg width="44" height="44" viewBox="0 0 44 44" fill="none" stroke="#fff" stroke-width="1.8"><circle cx="19" cy="19" r="12"/><path d="M28 28l10 10M12 23l5-6 4 4 6-8"/></svg></div>
    <h3>Optimse&amp;Manage</h3>
    <p>Our Managed Services delivers proactive, on-demand support for EPM and Data Analytics environments:</p>
    <a class="read-more" href="#">Read more &#10230;</a>
  </div>
</section>

<!-- how we do it -->
<section id="how">
  <div class="section-mark" style="top:1676px"></div>
  <h2 class="section-title" style="top:1721px">How we do it</h2>

  <svg class="abs" style="left:0;top:1830px" width="600" height="280" aria-hidden="true" fill="none" stroke="#2b5468" stroke-width="2.5">
    <path d="M408 58L465 25"/><path d="M433 140H513"/><path d="M411 226L463 242"/>
    <g fill="#2b5468" stroke="none"><circle cx="408" cy="58" r="3"/><circle cx="465" cy="25" r="3"/><circle cx="433" cy="140" r="3"/><circle cx="513" cy="140" r="3"/><circle cx="411" cy="226" r="3"/><circle cx="463" cy="242" r="3"/></g>
  </svg>
  <div class="hub"><div class="dot"></div><span>Meridale Partners</span></div>

  <div class="node" style="left:464px;top:1838px"></div>
  <div class="node" style="left:524px;top:1953px"></div>
  <div class="node" style="left:474px;top:2062px"></div>

  <div class="step-icon" style="left:522px;top:1788px"><svg width="40" height="40" viewBox="0 0 40 40" fill="none" stroke="#2b5468" stroke-width="1.6"><path d="M14 26a10 10 0 1 1 12 0v4H14z"/><path d="M15 34h10"/><circle cx="20" cy="17" r="4" stroke="#d96a34"/></svg></div>
  <div class="step abs" style="left:628px;top:1792px"><h4>Idea</h4><p>Lorem Ipsum is simply dummy text of the printing and typesetting industry.</p></div>

  <div class="step-icon" style="left:579px;top:1924px"><svg width="40" height="40" viewBox="0 0 40 40" fill="none" stroke="#2b5468" stroke-width="1.6"><path d="M12 34v-6a10 10 0 1 1 14 0l-1 6"/><circle cx="15" cy="13" r="4" stroke="#d96a34"/></svg></div>
  <div class="step abs" style="left:687px;top:1930px"><h4>Strategy</h4><p>Lorem Ipsum is simply dummy text of the printing and typesetting industry.</p></div>

  <div class="step-icon" style="left:521px;top:2062px"><svg width="40" height="40" viewBox="0 0 40 40" fill="none" stroke="#2b5468" stroke-width="1.6"><circle cx="20" cy="9" r="5" stroke="#d96a34"/><path d="M20 14v8M10 22h20"/><circle cx="9" cy="28" r="3"/><circle cx="20" cy="28" r="3"/><circle cx="31" cy="28" r="3"/><path d="M4 36a5 5 0 0 1 10 0M15 36a5 5 0 0 1 10 0M26 36a5 5 0 0 1 10 0"/></svg></div>
  <div class="step abs" style="left:628px;top:2070px"><h4>Team Work</h4><p>Lorem Ipsum is simply dummy text of the printing and typesetting industry.</p></div>
</section>

<!-- contact band -->
<section id="contact">
  <svg class="cta-art" viewBox="0 0 1200 430" aria-hidden="true">
    <path d="M0 130Q300 -10 760 35L1200 330V430H0Z" fill="#d96a34"/>
    <path d="M0 130Q200 40 420 22Q150 30 0 100Z" fill="#1b2f3c"/>
  </svg>
  <h2 class="cta-title">Contact Us to Discuss Your Business Needs</h2>
  <p class="cta-text">Lorem Ipsum is simply dummy text of the printing and typesetting industry. Lorem Ipsum has been the industry's</p>
  <a class="pill pill-navy abs" style="left:60px;top:2489px" href="#">
    <svg width="18" height="18" viewBox="0 0 24 24" fill="none" stroke="#fff" stroke-width="1.8"><path d="M5 3h4l2 5-3 2a12 12 0 0 0 6 6l2-3 5 2v4a2 2 0 0 1-2 2A17 17 0 0 1 3 5a2 2 0 0 1 2-2z"/></svg>01 555 0142</a>
  <a class="pill pill-white abs" style="left:217px;top:2489px" href="#">READ MORE
    <svg width="28" height="14" viewBox="0 0 28 14" fill="none" stroke="#1e3342" stroke-width="1.6"><circle cx="7" cy="7" r="5.5"/><path d="M7 7h19M21 2l5 5-5 5"/></svg></a>
  <div class="cta-photo" role="img" aria-label="Support advisor wearing a headset, framed in a teal circle"></div>
</section>

<!-- footer -->
<footer class="footer">
  <div class="brand" style="left:61px;top:50px"><span class="dot"></span><span>Meridale<br>Partners</span></div>
  <p class="abs" style="left:61px;top:126px;width:250px;font-size:12px;line-height:21px">MP are a Data Analytics &amp; EPM company, specialising in the implementation.</p>
  <div class="abs" style="left:60px;top:192px;display:flex;gap:14px">
    <a class="social" href="#" aria-label="Social profile" style="border:2px solid #fff"></a>
    <a class="social" href="#" aria-label="Social profile" style="background:var(--orange)"></a>
  </div>

  <div class="abs" style="left:338px;top:62px">
    <h5>Quick Links</h5>
    <ul style="margin-top:16px"><li>Who we are</li><li>What we do</li><li>How we do it</li><li>Contact us</li></ul>
  </div>

  <div class="abs" style="left:615px;top:62px">
    <h5>Contact Us</h5>
    <div class="contact-row" style="margin-top:16px">
      <svg width="20" height="20" viewBox="0 0 24 24" fill="none" stroke="#fff" stroke-width="1.6"><path d="M12 22s7-7 7-12a7 7 0 0 0-14 0c0 5 7 12 7 12z"/><circle cx="12" cy="10" r="2.5"/></svg>
      <span>14 Harrow Quay, Ashbrook,<br>Dublin 8, D08 KX21</span></div>
    <div class="contact-row" style="margin-top:12px;font-weight:600">
      <svg width="20" height="20" viewBox="0 0 24 24" fill="none" stroke="#fff" stroke-width="1.6"><path d="M5 3h4l2 5-3 2a12 12 0 0 0 6 6l2-3 5 2v4a2 2 0 0 1-2 2A17 17 0 0 1 3 5a2 2 0 0 1 2-2z"/></svg>
      <span>01 555 0142</span></div>
    <div class="contact-row" style="margin-top:18px">
      <svg width="20" height="20" viewBox="0 0 24 24" fill="none" stroke="#fff" stroke-width="1.6"><rect x="2" y="5" width="20" height="14"/><path d="M2 5l10 8 10-8"/></svg>
      <span>info@meridale-partners.example</span></div>
  </div>

  <div class="abs" style="left:891px;top:62px">
    <h5>Our Partner</h5>
    <div class="partner" style="margin-top:16px"><b>Quillmarsh</b><i></i><span>Partner</span></div>
  </div>
</footer>
<div class="bottom-bar">2022&copy; <b>MERIDALE PARTNERS</b>. All right reserved.</div>

</body>
</html>
```